Satchel & Sundial needs new business card design

I need a new business card design. I'm looking for out-of-the-box design which represents the freedom of being a location independent entrepreneur.
I offer coaching, retreats and trips.
I would like to see designs with and without the photo.
Colors I use are black (#000000), green (#25A796) and brown (#D7C38C)
Website satchelandsundial.example

Target Market(s)

location independent entrepreneurs, digital nomads, people looking to swap the 9 to 5 for a lifestyle business

Industry/Entity Type

Business

Contact Information for Business Card

Dorota Falkner
Your Lifestyle Business Coach, Retreat & Trip Leader
http://satchelandsundial.example
hello@satchelandsundial.example
Live a life you don't need a holiday from

Font styles to use
Serif
Sans Serif

Requirements
Must have
• One side should contain only the logo. I would also consider having the "Live a life you don't need a holiday from" on that side too (depending on how it looks)
• Please show both sides on the designs.

```html
<!DOCTYPE html>
<html lang="en">
<head>
<meta charset="utf-8">
<title>Satchel &amp; Sundial – Business Card</title>
<link href="https://fonts.googleapis.com/css2?family=Lora:wght@600&family=Domine:wght@400&family=Montserrat:wght@400&display=swap" rel="stylesheet">
<style>
  :root {
    --ink: #000000;
    --teal: #25A796;
    --sand: #D7C38C;
    --panel: #E6E7E8;
    --paper: #FFFFFF;
    --leaf-dark: #4d5a3a;
    --leaf-light: #a9b58a;
  }
  * { margin: 0; padding: 0; box-sizing: border-box; }
  html, body { width: 1200px; height: 1002px; overflow: hidden; background: var(--paper); }
  .stage {
    position: absolute; left: 0; top: 75px; width: 1200px; height: 927px;
    background: var(--panel); border: 1px solid #222;
  }
  .card {
    position: absolute; top: 65px; width: 456px; height: 798px;
    background: var(--paper); border-radius: 24px; overflow: hidden;
    box-shadow: 8px 8px 6px rgba(0,0,0,0.35);
  }
  .card--front { left: 119px; }
  .card--back { left: 623px; }
  .card__hero { position: absolute; left: 0; top: 0; width: 456px; height: 430px; display: block; }
  .wordmark {
    position: absolute; left: 0; width: 100%; text-align: center;
    font-family: "Lora", serif; font-weight: 600; color: var(--ink);
    letter-spacing: 0.5px;
  }
  .card--front .wordmark { top: 448px; font-size: 40px; }
  .card--back .wordmark { top: 330px; font-size: 44px; }
  .holder {
    position: absolute; top: 566px; left: 0; width: 100%; text-align: center;
    font-family: "Domine", serif; font-size: 35px; color: var(--teal); line-height: 40px;
  }
  .role {
    position: absolute; top: 609px; left: 0; width: 100%; text-align: center;
    font-family: "Montserrat", sans-serif; font-size: 19px; line-height: 25px; color: var(--ink);
  }
  .icons { position: absolute; top: 671px; left: 0; width: 100%; display: flex; justify-content: center; gap: 6px; }
  .icons svg { width: 13px; height: 13px; }
  .contact {
    position: absolute; top: 698px; left: 0; width: 100%; text-align: center;
    font-family: "Montserrat", sans-serif; font-size: 19px; line-height: 25.5px; color: var(--ink);
  }
  .contact .accent { color: var(--teal); }
  .tagline {
    position: absolute; top: 450px; left: 0; width: 100%; text-align: center;
    font-family: "Montserrat", sans-serif; font-size: 22px; line-height: 28px;
    letter-spacing: 1px; text-transform: uppercase; color: var(--ink);
  }
</style>
</head>
<body>
<div class="stage">
  <section class="card card--front">
    <svg class="card__hero" viewBox="0 0 456 430" aria-hidden="false">
      <defs>
        <linearGradient id="foliage" x1="0" y1="0" x2="1" y2="1">
          <stop offset="0" stop-color="#6f7f4c"/>
          <stop offset="0.5" stop-color="var(--leaf-light)"/>
          <stop offset="1" stop-color="var(--leaf-dark)"/>
        </linearGradient>
      </defs>
      <path role="img" aria-label="Photo of the coach sitting on a wooden rail beneath trees, holding a small sign"
            d="M0 0 H456 V350 C380 330 300 340 230 370 C150 405 60 400 0 386 Z" fill="url(#foliage)"/>
      <path d="M0 386 C60 400 150 405 230 370 C300 340 380 330 456 350 V388 C380 372 300 380 230 400 C150 425 60 428 0 420 Z"
            fill="var(--teal)"/>
    </svg>

    <div class="wordmark">Satchel &amp; Sundial</div>

    <h1 class="holder">Dorota Falkner</h1>
    <p class="role">Your Lifestyle Business Coach<br>Retreat &amp; Trip Leader</p>

    <div class="icons">
      <svg viewBox="0 0 16 16"><path d="M4 1 L6.5 4.5 L5 6 C6 8.5 7.5 10 10 11 L11.5 9.5 L15 12 L13 15 C7 14 2 9 1 3 Z" fill="none" stroke="var(--teal)" stroke-width="1.4"/></svg>
      <svg viewBox="0 0 16 16"><rect x="1.5" y="3.5" width="13" height="9" fill="none" stroke="var(--teal)" stroke-width="1.4"/><path d="M1.5 3.5 L8 9 L14.5 3.5" fill="none" stroke="var(--teal)" stroke-width="1.4"/></svg>
      <svg viewBox="0 0 16 16" fill="none" stroke="var(--teal)" stroke-width="1.2"><circle cx="8" cy="8" r="6.5"/><ellipse cx="8" cy="8" rx="3" ry="6.5"/><path d="M1.5 8 H14.5 M2.5 4.5 H13.5 M2.5 11.5 H13.5"/></svg>
    </div>

    <address class="contact" style="font-style:normal">
      +330 2470-5193<br>
      hello@satchelandsundial.example<br>
      www.<span class="accent">satchelandsundial</span>.example
    </address>
  </section>

  <section class="card card--back">
    <div class="wordmark">Satchel &amp; Sundial</div>
    <p class="tagline">Live a life you don’t<br>need a holiday from</p>
  </section>
</div>
</body>
</html>
```